Personal Trainer website design

We are working with a personal trainer to design a website. They offer their primary services: Diet Coaching, In-Person Coaching (workouts), and Remote Coaching.
Some sites we like: https://www.mirabelthorne.com, https://kavialune.com/en-us, https://corvexfit.co.uk
Thank you for taking the time to consider designing a website for us. We are web developers based in Stockton, CA USA. Most of our projects go through the same process. Understanding this process may help you win a project with us. We custom-code all of our websites in-house. We don’t have any requirements as to what tools you use for your design, but ask that you follow these guidelines.
IMAGES:
We ask that if you use any images, or icons in the design, have a link to the asset, so we can purchase the image/icon. Most of the designs we submit do not have the customer’s images on them unless they have some great images. Be creative; show us the feeling that you are trying to portray with your image choices. Use any royalty-free site you choose. We subscribe to Quillon and mostly use their images, but are ok to purchase images outside of Quillon.
FONTS:
We ask that you identify the fonts you’re using in the design. This can be done in a message if you want. We typically use Brivane Fonts and Quillon Fonts.
CONTENT:
We're always open to different content and ideas. Often, we submit designs with stock images so that the client can see our vision. We typically go back and take pictures after the website launch to use their images with our vision. Lorem Ipsum is fine for paragraphs, but we ask that you make the Headers with correct English. We want to be able to show the vision and identify the sections of the website.
INSPIRATION:
We try and add a couple of links in the brief of some websites that we like to help you get started in your design.
REVISIONS:
We do not often ask for revisions of the designs unless we see something in the design that may not appeal to the client. If there are slight changes that we want to make, we simply do that in the development process.
FEEDBACK:
We rarely give feedback on designs during the design process. We are working on many website projects and do not have the time to give feedback. We usually respond if your request is well thought out and asks specific questions, but a note asking “feedback, please” usually goes unanswered.
1 page

```html
<!DOCTYPE html>
<html lang="en">
<head>
<meta charset="utf-8">
<title>Orbivofit — Personal Training</title>
<link href="https://fonts.googleapis.com/css2?family=Roboto+Condensed:wght@400;700&family=Roboto:wght@400;500;700&family=Open+Sans:wght@400;600&display=swap" rel="stylesheet">
<style>
:root{
  --green:#93a81f;
  --green-dark:#7f9218;
  --wine:#7a1510;
  --wine-deep:#5e0f0b;
  --olive:#6a5c45;
  --ink:#2a2a2a;
  --muted:#777;
  --footer:#1d1d1d;
  --white:#fff;
}
*{box-sizing:border-box;margin:0;padding:0}
html,body{width:1200px;height:4197px;overflow:hidden;background:#fff}
body{position:relative;font-family:'Roboto',sans-serif;color:var(--ink)}
.abs{position:absolute}
.head{font-family:'Roboto Condensed',sans-serif;font-weight:700;text-transform:uppercase}
.bar{display:flex;align-items:center;gap:4px}
.bar i{display:block;height:4px;background:var(--green)}
.bar i.dot{width:6px;background:var(--wine)}
.btn{position:absolute;display:flex;align-items:center;justify-content:center;gap:10px;border-radius:30px;color:#fff;font-family:'Roboto Condensed',sans-serif;font-weight:700;font-size:16px;text-transform:uppercase}
.photo{position:absolute}

/* nav */
.brand{left:122px;top:24px;font-family:'Roboto Condensed',sans-serif;font-weight:700;font-size:40px;letter-spacing:1px;color:#222;display:flex;align-items:center;gap:10px}
.brand .mark{width:16px;height:16px;border-radius:50%;background:var(--green)}
.nav{left:437px;top:42px;display:flex;gap:28px;font-family:'Roboto Condensed',sans-serif;font-weight:700;font-size:15px;color:#222}
.nav .on{color:var(--green)}
.login{left:946px;top:31px;width:141px;height:42px;background:var(--green)}

/* hero */
.hero{left:5px;top:95px;width:1190px;height:624px;border-radius:90px 90px 90px 90px;overflow:hidden;
  background:linear-gradient(100deg,#c9b7a6 0%,#e4d9cc 30%,#b7a58f 55%,#7b6a55 78%,#4e4233 100%)}
.hero-copy{left:743px;top:285px;color:#fff}
.hero-copy .sm{font-size:42px;line-height:1}
.hero-copy .lg{font-size:92px;line-height:1;margin-top:18px}

/* about */
.about-h{left:109px;top:800px;font-size:36px}
.about-lead{left:109px;top:868px;width:403px;font-family:'Roboto Condensed',sans-serif;font-weight:700;font-size:19px;line-height:35px;color:var(--olive);text-align:justify}
.about-text{left:601px;top:798px;width:485px;font-family:'Open Sans',sans-serif;font-size:14px;line-height:25.6px;color:#888;text-align:justify}

/* services */
.services{left:0;top:1451px;width:1200px;height:450px;background:linear-gradient(180deg,#98ae23,#8da11c)}
.card{position:absolute;width:308px;background:#fff;border-radius:10px;box-shadow:0 6px 18px rgba(0,0,0,.15);text-align:center}
.card .img{position:absolute;left:8px;top:8px;right:8px;height:228px;border-radius:2px}
.card .ico{position:absolute;left:50%;top:200px;width:70px;height:70px;margin-left:-35px;border-radius:50%;border:4px solid #fff;display:flex;align-items:center;justify-content:center}
.card h3{position:absolute;top:282px;width:100%;font-family:'Roboto Condensed',sans-serif;font-size:17px;font-weight:700}
.card p{position:absolute;top:315px;left:28px;right:28px;font-family:'Open Sans',sans-serif;font-size:13.5px;line-height:22px;color:#777}
.card .btn{left:84px;top:400px;width:141px;height:41px}

/* why */
.why-h{left:117px;top:2212px;font-size:36px}
.why-item{position:absolute;left:117px;width:430px}
.why-item .c{position:absolute;left:0;top:4px;width:60px;height:60px;border-radius:50%;background:#efe9e6;display:flex;align-items:center;justify-content:center}
.why-item h4{position:absolute;left:80px;top:0;font-size:17px;font-weight:700}
.why-item p{position:absolute;left:80px;top:32px;width:350px;font-family:'Open Sans',sans-serif;font-size:14px;line-height:23px;color:#888}

/* testimonials */
.testi{left:0;top:2706px;width:1200px;height:435px;background:linear-gradient(100deg,var(--wine-deep),var(--wine) 50%,#8a1d14)}
.quote{position:absolute;color:#fff}
.quote .ph{position:absolute;width:164px;height:164px;border-radius:50%;border:4px solid #fff;background:linear-gradient(160deg,#cfd6de,#5d6b7b)}
.quote .qm{position:absolute;width:56px;height:56px;border-radius:50%;background:var(--green);border:3px solid #fff;font-family:Georgia,serif;font-size:40px;font-weight:700;display:flex;align-items:center;justify-content:center;line-height:1;padding-top:14px}
.quote .stars{position:absolute;display:flex;gap:3px}
.quote p{position:absolute;width:295px;font-family:'Open Sans',sans-serif;font-style:italic;font-size:14.5px;line-height:24px}
.quote b{position:absolute;font-size:15px}

/* blog */
.blog-h{left:0;width:1200px;text-align:center;top:3222px;font-size:36px}
.post{position:absolute;top:3304px;width:308px;height:386px;background:#fff;border-radius:8px;box-shadow:0 4px 16px rgba(0,0,0,.12);text-align:center}
.post .img{position:absolute;left:8px;top:8px;right:8px;height:204px}
.post .date{position:absolute;top:232px;width:100%;display:flex;justify-content:center;align-items:center;gap:6px;font-size:13.5px;color:var(--wine)}
.post h3{position:absolute;top:256px;width:100%;font-size:17px;font-weight:700}
.post p{position:absolute;top:290px;left:22px;right:22px;font-family:'Open Sans',sans-serif;font-size:13.5px;line-height:22px;color:#888}
.post .more{position:absolute;top:346px;width:100%;display:flex;justify-content:center;align-items:center;gap:6px;font-family:'Roboto Condensed',sans-serif;font-weight:700;font-size:15px;color:var(--green)}

/* footer */
.footer{left:0;top:3775px;width:1200px;height:422px;background:var(--footer);color:#fff}
.f-brand{position:absolute;left:118px;top:170px;font-family:'Roboto Condensed',sans-serif;font-weight:700;font-size:34px;display:flex;align-items:center;gap:10px}
.f-brand .mark{width:18px;height:18px;border-radius:50%;background:var(--green)}
.f-col{position:absolute;top:88px}
.f-col h5{font-family:'Roboto Condensed',sans-serif;font-weight:700;font-size:15px;text-transform:uppercase}
.f-col h5+.ln{width:60px;height:2px;background:var(--green);margin-top:8px}
.links{list-style:none;margin-top:20px;font-size:12px;line-height:26px;padding-left:6px}
.contact{margin-top:14px;font-size:12px}
.contact div{display:flex;align-items:flex-start;gap:12px;margin-bottom:14px;line-height:18px}
.contact .ci{flex:none;width:24px;height:24px;border-radius:50%;background:#555;display:flex;align-items:center;justify-content:center}
.sub p{margin-top:20px;width:250px;font-size:12px;line-height:19px;padding-left:6px}
.sub .field{margin-top:14px;width:252px;height:34px;border-radius:20px;background:#fff;display:flex;align-items:center;overflow:hidden}
.sub .field span{flex:1;padding-left:16px;font-size:11px;color:#888}
.sub .field i{width:48px;height:34px;background:var(--green);display:flex;align-items:center;justify-content:center}
.social{display:flex;gap:9px;margin-top:14px}
.social i{width:30px;height:30px;border-radius:50%;background:#fff;display:block}
.social i.g{background:var(--green)}
.chat{position:absolute;right:30px;top:293px;width:42px;height:42px;border-radius:50%;background:var(--green);display:flex;align-items:center;justify-content:center}
.bottom{position:absolute;left:0;top:364px;width:1200px;height:58px;border-top:1px solid #333;font-size:13px;display:flex;align-items:center;padding:0 110px}
.bottom .l{flex:1}
.bottom .l u{color:#fff;font-weight:700}
.bottom .r{display:flex;gap:14px}
</style>
</head>
<body>

<!-- header -->
<div class="abs brand"><span>ORBIVOFIT</span><span class="mark"></span></div>
<nav class="abs nav">
  <span class="on">HOME</span><span>ABOUT US</span><span>SERVICES</span><span>TESTIMONIALS</span><span>CONTACT US</span>
</nav>
<div class="btn login">Login
  <svg width="13" height="14" viewBox="0 0 13 14"><circle cx="6.5" cy="4" r="3.5" fill="#fff"/><path d="M0 14c0-4 3-6 6.5-6S13 10 13 14z" fill="#fff"/></svg>
</div>

<!-- hero -->
<div class="abs hero" role="img" aria-label="Smiling woman in sportswear eating a salad in a bright home gym"></div>
<div class="abs hero-copy head">
  <div class="sm">Welcome to</div>
  <div class="lg">Orbivofit</div>
</div>
<div class="btn" style="left:743px;top:478px;width:154px;height:40px;background:var(--green);font-size:15px">Get Started
  <svg width="14" height="14" viewBox="0 0 14 14"><circle cx="7" cy="7" r="7" fill="#fff"/><path d="M4 7h6M7.5 4.5 10 7l-2.5 2.5" stroke="var(--green)" stroke-width="1.6" fill="none"/></svg>
</div>
<div class="btn" style="left:916px;top:478px;width:166px;height:40px;background:var(--wine);font-size:15px">Play Now
  <svg width="14" height="14" viewBox="0 0 14 14"><circle cx="7" cy="7" r="7" fill="#fff"/><path d="M5.5 4v6l5-3z" fill="var(--wine)"/></svg>
</div>

<!-- about -->
<h2 class="abs head about-h">About Orbivofit</h2>
<div class="abs bar" style="left:109px;top:846px"><i style="width:30px"></i><i class="dot"></i><i style="width:30px"></i></div>
<p class="abs about-lead">Lorem ipsum dolor sited ameted consectetur adipiscing elited sed do eiusmod tempor incididunt uted labore et dolore magna aliqua Ut enim ad minim veniam,</p>
<p class="abs about-text">Sed ut perspiciatis unde omnis iste natus error sit voluptatem accusantium doloremque laudantium, totam rem aperiam, eaque ipsa quae ab illo inventore veritatis et quasi architecto beatae vitae dicta sunt explicabo. Nemo enim ipsam voluptatem quia voluptas sit aspernatur aut odit aut fugit, sed quia consequuntur magni dolores eos qui ratione voluptatem sequi nesciunt Neque porro quisquam.</p>
<svg class="abs" style="left:558px;top:1006px" width="375" height="336" viewBox="0 0 375 336">
  <path d="M3 36V3h40" stroke="var(--green)" stroke-width="6" fill="none"/>
  <path d="M372 290v43H140" stroke="var(--green)" stroke-width="6" fill="none"/>
</svg>
<div class="photo" style="left:601px;top:981px;width:486px;height:324px;background:linear-gradient(120deg,#9a8a7d,#d9d4cf 45%,#b8b3ad 70%,#6e6a64)" role="img" aria-label="Smiling coach in a white blazer at a desk during a consultation"></div>
<div class="photo" style="left:109px;top:1051px;width:590px;height:313px;border:5px solid #fff;box-shadow:0 4px 14px rgba(0,0,0,.15);background:linear-gradient(100deg,#6d6660,#b5aea8 40%,#e6e2de 65%,#8c8884)" role="img" aria-label="Woman doing sit-ups with a trainer in a gym"></div>

<!-- services -->
<div class="abs services" role="img" aria-label="Green tinted band with a trainer working out in the background"></div>
<h2 class="abs head" style="left:0;width:1200px;text-align:center;top:1512px;font-size:36px;color:#fff">Our Services</h2>
<div class="abs bar" style="left:566px;top:1566px"><i style="width:30px;background:#fff"></i><i class="dot"></i><i style="width:30px;background:#fff"></i></div>

<div class="card" style="left:111px;top:1622px;height:470px">
  <div class="img" role="img" aria-label="Couple sharing a healthy meal in a gym" style="background:linear-gradient(130deg,#4b4a42,#a49f84 50%,#394b55)"></div>
  <div class="ico" style="background:var(--olive)"><svg width="30" height="30" viewBox="0 0 30 30" fill="none" stroke="#fff" stroke-width="2"><path d="M4 16h22a11 11 0 0 1-22 0z"/><path d="M10 12c0-3 2-5 5-5s5 2 5 5"/></svg></div>
  <h3>Diet Coaching</h3>
  <p>Lorem ipsum dolor sit amet, consectetur adipiscing elit, sed do eiusmod tempor incididunt uted labore eted.</p>
  <div class="btn" style="background:var(--olive)">Read More</div>
</div>
<div class="card" style="left:445px;top:1638px;height:470px">
  <div class="img" role="img" aria-label="Trainer with clipboard beside a client on a weight bench" style="background:linear-gradient(130deg,#cfcfcf,#6b6f77 50%,#2e3036)"></div>
  <div class="ico" style="background:var(--green)"><svg width="30" height="30" viewBox="0 0 30 30" fill="none" stroke="#fff" stroke-width="2"><path d="M4 24h22M8 20l6-8 4 4 6-8"/></svg></div>
  <h3>In-Person Coaching</h3>
  <p>Lorem ipsum dolor sit amet, consectetur adipiscing elit, sed do eiusmod tempor incididunt uted labore eted.</p>
  <div class="btn" style="background:var(--green)">Read More</div>
</div>
<div class="card" style="left:779px;top:1622px;height:470px">
  <div class="img" role="img" aria-label="Coach waving during a video call at a laptop" style="background:linear-gradient(130deg,#6f7072,#d6d6d4 55%,#9a9a96)"></div>
  <div class="ico" style="background:var(--wine)"><svg width="30" height="30" viewBox="0 0 30 30" fill="none" stroke="#fff" stroke-width="2"><rect x="5" y="6" width="20" height="14" rx="1"/><path d="M2 24h26"/></svg></div>
  <h3>Remote Coaching</h3>
  <p>Lorem ipsum dolor sit amet, consectetur adipiscing elit, sed do eiusmod tempor incididunt uted labore eted.</p>
  <div class="btn" style="background:var(--wine)">Read More</div>
</div>

<!-- why choose us -->
<h2 class="abs head why-h">Why Choose Us</h2>
<div class="abs bar" style="left:117px;top:2258px"><i style="width:30px"></i><i class="dot"></i><i style="width:30px"></i></div>
<div class="why-item" style="top:2306px">
  <div class="c"><svg width="28" height="28" viewBox="0 0 28 28" fill="none" stroke="var(--wine)" stroke-width="1.6"><rect x="6" y="4" width="16" height="20" rx="2"/><path d="M10 10h8M10 14h8M10 18h5"/></svg></div>
  <h4>Lorem ipsum dolor sit consectetur</h4>
  <p>Lorem ipsum dolor sit amet, consectetur adipiscing elit, sed do eiusmod tempor incididunt</p>
</div>
<div class="why-item" style="top:2409px">
  <div class="c"><svg width="28" height="28" viewBox="0 0 28 28" fill="none" stroke="var(--wine)" stroke-width="1.6"><path d="M3 14h22M6 9v10M22 9v10M9 11v6M19 11v6"/></svg></div>
  <h4>Lorem ipsum dolor sit consectetur</h4>
  <p>Lorem ipsum dolor sit amet, consectetur adipiscing elit, sed do eiusmod tempor incididunt</p>
</div>
<div class="why-item" style="top:2512px">
  <div class="c"><svg width="28" height="28" viewBox="0 0 28 28" fill="none" stroke="var(--wine)" stroke-width="1.6"><rect x="4" y="5" width="20" height="15" rx="1"/><path d="M9 24h10M14 20v4M8 15l4-4 3 3 5-5"/></svg></div>
  <h4>Lorem ipsum dolor sit consectetur</h4>
  <p>Lorem ipsum dolor sit amet, consectetur adipiscing elit, sed do eiusmod tempor incididunt</p>
</div>
<div class="photo" style="left:628px;top:2194px;width:459px;height:426px;border:4px solid #fff;box-shadow:0 4px 16px rgba(0,0,0,.18);background:linear-gradient(120deg,#2f6a8a,#8fb1bd 40%,#e0d2c4 65%,#a66a3a)" role="img" aria-label="Smiling woman planning meals at a table with fresh vegetables"></div>

<!-- testimonials -->
<div class="abs testi" role="img" aria-label="Deep red band with a faint workout scene"></div>
<h2 class="abs head" style="left:0;width:1200px;text-align:center;top:2786px;font-size:36px;color:#fff">What Our Client Says</h2>
<div class="abs bar" style="left:566px;top:2836px"><i style="width:30px"></i><i class="dot" style="background:#fff"></i><i style="width:30px"></i></div>

<div class="quote" style="left:0;top:0">
  <div class="ph" style="left:110px;top:2885px" role="img" aria-label="Client portrait, man in a suit"></div>
  <div class="qm" style="left:166px;top:3016px">“</div>
  <div class="stars" style="left:297px;top:2880px">
    <svg width="82" height="14" viewBox="0 0 82 14" fill="#f3c316"><g id="st"><path d="M7 0l2 5h5l-4 3 1.5 5L7 10l-4.5 3L4 8 0 5h5z"/></g><use href="#st" x="17"/><use href="#st" x="34"/><use href="#st" x="51"/><use href="#st" x="68"/></svg>
  </div>
  <p style="left:297px;top:2906px">"Lorem ipsum dolor sit wamet consectetured adipiscing sed do eiusmod tempor incididunt labore eted dolore magna aliquat enim minim veniam quised nostrud exercitation ullamced laboris nisi ut aliquip ex ea commodo"</p>
  <b style="left:297px;top:3044px">John Doe</b>
</div>
<div class="quote" style="left:0;top:0">
  <div class="ph" style="left:619px;top:2873px;background:linear-gradient(160deg,#c7c9c5,#46504e)" role="img" aria-label="Client portrait, smiling man in a jacket"></div>
  <div class="qm" style="left:675px;top:3004px">“</div>
  <div class="stars" style="left:802px;top:2868px">
    <svg width="82" height="14" viewBox="0 0 82 14" fill="#f3c316"><use href="#st"/><use href="#st" x="17"/><use href="#st" x="34"/><use href="#st" x="51"/><use href="#st" x="68"/></svg>
  </div>
  <p style="left:802px;top:2894px">"Lorem ipsum dolor sit wamet consectetured adipiscing sed do eiusmod tempor incididunt labore eted dolore magna aliquat enim minim veniam quised nostrud exercitation ullamced laboris nisi ut aliquip ex ea commodo"</p>
  <b style="left:802px;top:3032px">John Doe</b>
</div>

<!-- blog -->
<h2 class="abs head blog-h">Latest Blog</h2>
<div class="abs bar" style="left:566px;top:3268px"><i style="width:30px"></i><i class="dot"></i><i style="width:30px"></i></div>

<div class="post" style="left:111px">
  <div class="img" role="img" aria-label="Trainer and client reviewing a tablet in a gym" style="background:linear-gradient(130deg,#3b3a36,#a08e6c 50%,#6a5f70)"></div>
  <div class="date"><svg width="12" height="12" viewBox="0 0 12 12"><rect x="1" y="2" width="10" height="9" rx="1" fill="var(--wine)"/><rect x="2" y="5" width="8" height="5" fill="#fff"/></svg>March 25, 2023</div>
  <h3>Lorem ipsum dolor sit amet</h3>
  <p>Sed ut perspiciatis unde omnis iste natus sit voluptatem accusantium</p>
  <div class="more">Read More <svg width="13" height="13" viewBox="0 0 14 14"><circle cx="7" cy="7" r="7" fill="var(--green)"/><path d="M4 7h6M7.5 4.5 10 7l-2.5 2.5" stroke="#fff" stroke-width="1.6" fill="none"/></svg></div>
</div>
<div class="post" style="left:445px">
  <div class="img" role="img" aria-label="Woman in a red sweater working on a laptop" style="background:linear-gradient(130deg,#c9d2d8,#eef0f1 50%,#b5493f)"></div>
  <div class="date"><svg width="12" height="12" viewBox="0 0 12 12"><rect x="1" y="2" width="10" height="9" rx="1" fill="var(--wine)"/><rect x="2" y="5" width="8" height="5" fill="#fff"/></svg>March 25, 2023</div>
  <h3>Lorem ipsum dolor sit amet</h3>
  <p>Sed ut perspiciatis unde omnis iste natus sit voluptatem accusantium</p>
  <div class="more">Read More <svg width="13" height="13" viewBox="0 0 14 14"><circle cx="7" cy="7" r="7" fill="var(--green)"/><path d="M4 7h6M7.5 4.5 10 7l-2.5 2.5" stroke="#fff" stroke-width="1.6" fill="none"/></svg></div>
</div>
<div class="post" style="left:779px">
  <div class="img" role="img" aria-label="Two women preparing vegetables in a bright kitchen" style="background:linear-gradient(130deg,#e8e6e0,#c8c1b3 50%,#6c7a3a)"></div>
  <div class="date"><svg width="12" height="12" viewBox="0 0 12 12"><rect x="1" y="2" width="10" height="9" rx="1" fill="var(--wine)"/><rect x="2" y="5" width="8" height="5" fill="#fff"/></svg>March 25, 2023</div>
  <h3>Lorem ipsum dolor sit amet</h3>
  <p>Sed ut perspiciatis unde omnis iste natus sit voluptatem accusantium</p>
  <div class="more">Read More <svg width="13" height="13" viewBox="0 0 14 14"><circle cx="7" cy="7" r="7" fill="var(--green)"/><path d="M4 7h6M7.5 4.5 10 7l-2.5 2.5" stroke="#fff" stroke-width="1.6" fill="none"/></svg></div>
</div>

<!-- footer -->
<footer class="abs footer">
  <div class="f-brand"><span class="mark"></span><span>ORBIVOFIT</span></div>

  <div class="f-col" style="left:370px">
    <h5>Quick Links</h5><div class="ln"></div>
    <ul class="links"><li>Home</li><li>About Us</li><li>Services</li><li>Testimonials</li><li>Contact Us</li></ul>
  </div>

  <div class="f-col" style="left:562px">
    <h5>Contact Us</h5><div class="ln"></div>
    <div class="contact">
      <div><span class="ci"><svg width="12" height="12" viewBox="0 0 12 12"><path d="M2 1l2.5 0 1 3-1.5 1a6 6 0 0 0 3 3l1-1.5 3 1V10a1 1 0 0 1-1 1A9 9 0 0 1 1 2a1 1 0 0 1 1-1z" fill="#fff"/></svg></span><span style="padding-top:3px">+1 888 888 8888</span></div>
      <div><span class="ci"><svg width="12" height="10" viewBox="0 0 12 10"><rect x=".5" y=".5" width="11" height="9" fill="none" stroke="#fff"/><path d="M.5 .5 6 5l5.5-4.5" fill="none" stroke="#fff"/></svg></span><span style="padding-top:3px">info@orbivofit.com</span></div>
      <div><span class="ci"><svg width="10" height="13" viewBox="0 0 10 13"><path d="M5 0a5 5 0 0 1 5 5c0 3-5 8-5 8S0 8 0 5a5 5 0 0 1 5-5z" fill="#fff"/><circle cx="5" cy="5" r="2" fill="#555"/></svg></span><span>45,Lorem ipsum dolor sit amet<br>&nbsp;consectetur adipiscing sed do</span></div>
      <div style="margin-top:14px"><span class="ci"><svg width="12" height="12" viewBox="0 0 12 12"><rect x="1" y="3" width="10" height="8" rx="1" fill="#fff"/><rect x="3" y="1" width="6" height="3" fill="none" stroke="#fff"/></svg></span><span style="padding-top:3px">123-456-7890</span></div>
    </div>
  </div>

  <div class="f-col sub" style="left:830px">
    <h5>Subscribe To Our Blog</h5><div class="ln"></div>
    <p>Sign up today to get resources on how to attract and retain more customers!</p>
    <div class="field"><span>✉ Email Address</span><i><svg width="16" height="14" viewBox="0 0 16 14"><path d="M0 6 16 0l-3 14-5-4-2 4V9l8-7-9 6z" fill="#fff"/></svg></i></div>
    <div class="social"><i></i><i class="g"></i><i></i><i></i><i></i></div>
  </div>

  <div class="chat"><svg width="20" height="18" viewBox="0 0 20 18"><path d="M10 1c5 0 9 3 9 7s-4 7-9 7l-5 3 1-4C3 13 1 11 1 8c0-4 4-7 9-7z" fill="#fff"/><circle cx="6.5" cy="8" r="1.2" fill="var(--green)"/><circle cx="10" cy="8" r="1.2" fill="var(--green)"/><circle cx="13.5" cy="8" r="1.2" fill="var(--green)"/></svg></div>

  <div class="bottom">
    <div class="l">Copyright© 2023 <u>Orbivofit.</u> &nbsp;|&nbsp; All Rights Reserved</div>
    <div class="r"><span>Terms &amp; Condition</span><span>|</span><span>Site Map</span><span>|</span><span>Privacy Policy</span></div>
  </div>
</footer>

</body>
</html>
```